Holiday Rental Leaflet

Want a DL size double sided leaflet to distribute via local businesses, markets, family and friends
HOLIDAY RENTALCarrickalinga - 17 Farrow Street Sleeps 8-10 (2 Queen, 1 Double, 2 bunks), 4 bedrooms, BIR to all bedrooms 2 Bathrooms, one with bath, 2 toilets Open Plan Lounge/Dining/Kitchen area Dining Table for 8 peopleReverse cycle airconditionerSlow combustion wood heaterTV/DVD, CD/RadioKitchen has m/wave, oven, fridge/freezer, dishwasherBBQ providedTimber decking with 2 outside tables and 12 chairs Washing Machine and dryer provided One street back from beach Smoke free zone No Pets
For further information or to book contact Joan on 0491 208 336 or email joanbriggs72@zentamail.com.au

Requirements
Nice to have
• Have sent a variety of photos of the house. No need to use all of them, pick out the most relevant for the leaflet.

```html
<!DOCTYPE html>
<html lang="en">
<head>
<meta charset="utf-8">
<title>Holiday Rental – Carrickalinga</title>
<link rel="stylesheet" href="https://fonts.googleapis.com/css2?family=Montserrat:wght@700&family=Source+Sans+3:wght@400;600;700&display=swap">
<style>
  :root {
    --teal: #2a9aa8;
    --teal-dark: #23899a;
    --orange: #f07b4f;
    --yellow: #f7d96a;
    --pink: #ee5f86;
    --ink: #1d1d1d;
    --paper: #ffffff;
  }
  * { margin: 0; padding: 0; box-sizing: border-box; }
  html, body { width: 850px; height: 1200px; overflow: hidden; background: var(--paper); }
  .leaflet {
    position: relative;
    width: 850px;
    height: 1200px;
    overflow: hidden;
    background: var(--paper);
    font-family: "Source Sans 3", "Myriad Pro", Arial, sans-serif;
    color: var(--ink);
  }
  .hero { position: absolute; top: 0; left: 0; width: 850px; height: 760px; display: block; }
  .title {
    position: absolute;
    top: 42px;
    left: 60px;
    white-space: nowrap;
    font-family: "Montserrat", Arial, sans-serif;
    font-weight: 700;
    font-size: 56px;
    letter-spacing: 0.5px;
    color: var(--paper);
    line-height: 1;
  }
  .title .place {
    font-family: "Source Sans 3", Arial, sans-serif;
    font-weight: 700;
    font-size: 36px;
    color: var(--orange);
    margin-left: 16px;
    letter-spacing: 0;
  }
  .features {
    position: absolute;
    top: 800px;
    left: 0;
    width: 850px;
    text-align: center;
    font-size: 17.5px;
    line-height: 23.5px;
  }
  .features p { margin-bottom: 8px; }
  .features .tight { margin-bottom: 0; }
  .label { color: var(--teal); font-weight: 700; }
  .dot {
    display: inline-block;
    width: 9px; height: 9px;
    background: var(--teal);
    transform: rotate(45deg) scaleY(1.35);
    margin: 0 6px 2px;
  }
  .rule {
    position: absolute;
    top: 1078px;
    left: 0;
    width: 850px;
    height: 3px;
    background: var(--teal);
  }
  .contact {
    position: absolute;
    top: 1086px;
    left: 0;
    width: 850px;
    text-align: center;
    font-size: 22px;
    line-height: 28px;
  }
  .contact strong { font-weight: 700; font-size: 25px; }
  .colour-bars { position: absolute; bottom: 0; left: 0; width: 850px; height: 50px; display: flex; }
  .colour-bars span { flex: 1; }
  .bar-teal { background: var(--teal); }
  .bar-yellow { background: var(--yellow); }
  .bar-orange { background: var(--orange); }
  .bar-pink { background: var(--pink); }
</style>
</head>
<body>
<main class="leaflet">
  <svg class="hero" viewBox="0 0 850 760" xmlns="http://www.w3.org/2000/svg">
    <defs>
      <clipPath id="lens">
        <path d="M0,175 Q425,60 850,175 L850,640 Q425,830 0,640 Z"/>
      </clipPath>
      <linearGradient id="bunkroom" x1="0" y1="0" x2="1" y2="1">
        <stop offset="0" stop-color="#6e5a45"/>
        <stop offset="0.5" stop-color="#8aa0b4"/>
        <stop offset="1" stop-color="#3d3a3a"/>
      </linearGradient>
      <linearGradient id="heater" x1="0" y1="0" x2="0" y2="1">
        <stop offset="0" stop-color="#d8b68a"/>
        <stop offset="0.55" stop-color="#8a7260"/>
        <stop offset="1" stop-color="#b8705a"/>
      </linearGradient>
      <linearGradient id="queenroom" x1="0" y1="0" x2="1" y2="1">
        <stop offset="0" stop-color="#a08466"/>
        <stop offset="0.6" stop-color="#e08a4a"/>
        <stop offset="1" stop-color="#5a4a40"/>
      </linearGradient>
      <linearGradient id="dining" x1="0" y1="0" x2="1" y2="1">
        <stop offset="0" stop-color="#d79a50"/>
        <stop offset="0.6" stop-color="#e6b070"/>
        <stop offset="1" stop-color="#c88a48"/>
      </linearGradient>
    </defs>
    <rect class="header-band" x="0" y="0" width="850" height="260" fill="var(--teal)"/>
    <g clip-path="url(#lens)">
      <rect x="0" y="0" width="850" height="760" fill="var(--paper)"/>
      <rect x="0" y="0" width="436" height="465" fill="url(#bunkroom)" role="img" aria-label="Photo of a bedroom with black iron bunk beds and striped bedding"/>
      <rect x="443" y="0" width="407" height="465" fill="url(#heater)" role="img" aria-label="Photo of a slow combustion wood heater against a stone wall"/>
      <rect x="0" y="471" width="436" height="289" fill="url(#queenroom)" role="img" aria-label="Photo of a queen bedroom with colourful striped bedspread and log walls"/>
      <rect x="443" y="471" width="407" height="289" fill="url(#dining)" role="img" aria-label="Photo of the timber-lined open plan dining area with table and chairs"/>
    </g>
  </svg>

  <h1 class="title">HOLIDAY RENTAL<span class="place">Carrickalinga</span></h1>

  <section class="features">
    <p><span class="label">Sleeps</span> 8-10 (2 Queen, 1 Double, 2 bunks), 4 bedrooms,<br>BIR to all bedrooms 2 Bathrooms, one with bath, 2 toilets</p>
    <p>Reverse cycle airconditioner<span class="dot"></span>Slow combustion wood heater<span class="dot"></span>TV/DVD<span class="dot"></span>CD/Radio</p>
    <p><span class="label">Open Plan Lounge</span>/Dining/Kitchen area<br>Dining Table for 8 people</p>
    <p class="tight"><span class="label">Kitchen has</span> m/wave, oven, fridge/freezer, dish washer<span class="dot"></span>BBQ provided</p>
    <p><span class="label">Timber decking</span> with 2 outside tables and 12 chairs<br>Washing Machine and dryer provided</p>
    <p>Smoke free zone<br>No Pets</p>
  </section>

  <div class="rule"></div>

  <footer class="contact">
    <p>For further information or to book</p>
    <p>contact Joan on <strong>0491 208 336</strong> or email joanbriggs72@zentamail.com.au</p>
  </footer>

  <div class="colour-bars">
    <span class="bar-teal"></span>
    <span class="bar-yellow"></span>
    <span class="bar-orange"></span>
    <span class="bar-pink"></span>
  </div>
</main>
</body>
</html>
```